Ridgeline Journeys business card

please see website
www.ridgelinejourneys.comau

info needed on card
Curtis Halvey
Ph
email
Adventure Riding GPS trails

please use my logo and colours off my site

Curtis Halvey
curtis@ridgelinejourneys.com

```html
<!DOCTYPE html>
<html lang="en">
<head>
<meta charset="utf-8">
<title>Ridgeline Journeys business card</title>
<link rel="stylesheet" href="https://fonts.googleapis.com/css2?family=Arimo:wght@400;700&display=swap">
<style>
  :root {
    --backdrop: #e4e2de;
    --card-white: #f7f7f5;
    --card-black: #0b0b0b;
    --brand-yellow: #f2d21c;
    --ink-dark: #1c1c1c;
    --ink-light: #ffffff;
    --rule-grey: #8a8a8a;
  }
  * { box-sizing: border-box; margin: 0; padding: 0; }
  html, body {
    width: 1200px; height: 892px; overflow: hidden;
    background: var(--backdrop);
    font-family: "Arimo", Arial, sans-serif;
  }
  .canvas {
    width: 1200px; height: 892px;
    display: flex; align-items: center; justify-content: center; gap: 60px;
  }
  .card {
    position: relative;
    width: 520px; height: 300px;
    background: var(--card-white);
    border-radius: 4px;
    box-shadow: 0 6px 18px rgba(0,0,0,0.18);
    overflow: hidden;
  }
  /* back side */
  .card-back .brand {
    position: absolute; inset: 0;
    display: flex; align-items: center; justify-content: center; gap: 18px;
  }
  .brand-dot {
    width: 52px; height: 52px; border-radius: 50%;
    background: var(--brand-yellow);
    flex: none;
  }
  .brand-name {
    font-weight: 700; color: var(--ink-dark);
    line-height: 1.02; text-transform: uppercase;
  }
  .card-back .brand-name { font-size: 40px; }

  /* front side */
  .front-shape { position: absolute; inset: 0; width: 100%; height: 100%; }
  .card-front .brand {
    position: absolute; top: 52px; right: 22px;
    display: flex; align-items: center; gap: 12px;
  }
  .card-front .brand-dot { width: 36px; height: 36px; }
  .card-front .brand-name { font-size: 26px; }
  .holder-name {
    position: absolute; left: 30px; top: 60px;
    color: var(--ink-light); font-size: 25px; font-weight: 400; letter-spacing: 0.3px;
    white-space: nowrap;
  }
  .contact {
    position: absolute; left: 30px; top: 226px;
    display: flex; align-items: center; gap: 12px;
  }
  .contact-rule { width: 1px; height: 50px; background: var(--rule-grey); }
  .contact-icons { display: flex; flex-direction: column; gap: 8px; }
  .contact-icons svg { display: block; }
  .contact-lines { display: flex; flex-direction: column; gap: 7px; }
  .contact-line { color: var(--ink-light); font-size: 15px; line-height: 18px; white-space: nowrap; }
</style>
</head>
<body>
<main class="canvas">

  <section class="card card-back" aria-label="Card back">
    <div class="brand">
      <span class="brand-dot"></span>
      <span class="brand-name">Ridgeline<br>Journeys</span>
    </div>
  </section>

  <section class="card card-front" aria-label="Card front">
    <svg class="front-shape" viewBox="0 0 520 300" preserveAspectRatio="none" aria-hidden="true">
      <path d="M0,0 L250,0 C260,150 360,240 520,262 L520,300 L0,300 Z" fill="var(--card-black)"/>
      <path d="M268,0 C280,140 372,228 520,250" fill="none" stroke="var(--brand-yellow)" stroke-width="4" stroke-linecap="round"/>
    </svg>

    <div class="brand">
      <span class="brand-dot"></span>
      <span class="brand-name">Ridgeline<br>Journeys</span>
    </div>

    <p class="holder-name">Curtis Halvey</p>

    <div class="contact">
      <span class="contact-rule"></span>
      <div class="contact-icons">
        <svg width="18" height="18" viewBox="0 0 18 18" aria-hidden="true">
          <rect x="0.5" y="0.5" width="17" height="17" rx="2" fill="var(--ink-light)"/>
          <rect x="3" y="5" width="12" height="8" fill="none" stroke="var(--card-black)" stroke-width="1.3"/>
          <path d="M3,5 L9,10 L15,5" fill="none" stroke="var(--card-black)" stroke-width="1.3"/>
        </svg>
        <svg width="18" height="18" viewBox="0 0 18 18" aria-hidden="true">
          <rect x="0.5" y="0.5" width="17" height="17" rx="2" fill="var(--ink-light)"/>
          <circle cx="9" cy="9" r="5.5" fill="none" stroke="var(--card-black)" stroke-width="1.3"/>
          <path d="M3.5,9 H14.5 M9,3.5 C6.5,6 6.5,12 9,14.5 M9,3.5 C11.5,6 11.5,12 9,14.5" fill="none" stroke="var(--card-black)" stroke-width="1.1"/>
        </svg>
      </div>
      <div class="contact-lines">
        <span class="contact-line">curtis@ridgelinejourneys.com</span>
        <span class="contact-line">www.ridgelinejourneys.comau</span>
      </div>
    </div>
  </section>

</main>
</body>
</html>
```